Business card for builder specialising in renovations.

Need a card for our building business. Business name is under Martin Powles.
Have licence number on card ( 527691K)
Contact number (0400 382 415)
Want to work on logo for some business cards and shirts - something with MP or MPB or open to ideas??
No animations, No hammers. Something sharp and eye catching.
Highlight that we are a renovation specialist. Simple on front with extra details on back with some lines to jot down things.

Target Market(s)

Renovators

Industry/Entity Type

Building

Contact Information for Business Card

2 sided with room on back to jot things down.
Extra details on back so front can be simple ..like, renovations, bathrooms, decks, extensions, new builds,

Logo Text

MP

Font styles to use
Serif

Requirements
Must have
• Eye catching design .
• Name : Martin powles
• Licence number
• Contact number - 0400382415
Nice to have
• Some logo design that we can carry through to other forms of advertising
• Local builder
• Quality work
Should not have
• No animations

```html
<!DOCTYPE html>
<html lang="en">
<head>
<meta charset="utf-8">
<title>Martin Powles – Business Card</title>
<link href="https://fonts.googleapis.com/css2?family=Noto+Serif:wght@400;700&display=swap" rel="stylesheet">
<style>
  :root {
    --bg: #2a2a2a;
    --card-black: #050505;
    --card-white: #ffffff;
    --accent-blue: #27a7e0;
    --ghost: #1c1c1c;
    --ink: #111111;
    --divider: #9a9a9a;
  }
  * { margin: 0; padding: 0; box-sizing: border-box; }
  html, body { width: 1200px; height: 900px; overflow: hidden; }
  body {
    background: var(--bg);
    font-family: "Noto Serif", Georgia, serif;
    position: relative;
  }
  .card {
    position: absolute;
    width: 700px;
    height: 400px;
    border-radius: 28px;
    overflow: hidden;
    box-shadow: 0 14px 30px rgba(0,0,0,.5);
  }

  /* Front */
  .card-front { left: 70px; top: 40px; background: var(--card-black); }
  .front-ghost-circle {
    position: absolute; left: 40px; top: 60px;
    width: 320px; height: 320px; border-radius: 50%;
    background: var(--ghost);
  }
  .front-badge {
    position: absolute; left: 215px; top: 135px;
    width: 170px; height: 170px; border-radius: 50%;
    background: var(--card-white);
    display: flex; align-items: center; justify-content: center;
    color: var(--ink); font-weight: 700; font-size: 64px;
  }
  .front-divider {
    position: absolute; left: 412px; top: 120px;
    width: 1px; height: 150px; background: var(--divider);
  }
  .front-name {
    position: absolute; left: 430px; top: 118px;
    color: var(--accent-blue); font-weight: 700;
    font-size: 44px; line-height: 1.05; text-transform: uppercase;
  }
  .front-name span { display: block; }
  .front-name .surname { padding-left: 28px; }
  .front-services {
    position: absolute; left: 60px; right: 30px; top: 330px;
    color: var(--card-white); font-size: 15px; letter-spacing: .3px;
    text-transform: uppercase; display: flex; gap: 8px; align-items: center;
    white-space: nowrap;
  }
  .service-dot {
    width: 10px; height: 10px; border-radius: 50%;
    background: var(--accent-blue); display: inline-block;
  }
  .front-web {
    position: absolute; left: 400px; top: 290px;
    color: var(--card-white); font-size: 18px;
  }
  .front-web .domain, .contact-web .domain { color: var(--accent-blue); }

  /* Back */
  .card-back { left: 430px; top: 470px; background: var(--card-white); }
  .back-disc {
    position: absolute; left: 330px; top: -150px;
    width: 470px; height: 470px; border-radius: 50%;
    background: var(--card-black);
    box-shadow: -5px 4px 0 var(--accent-blue);
  }
  .back-badge {
    position: absolute; left: 430px; top: 10px;
    width: 270px; height: 270px; border-radius: 50%;
    background: var(--accent-blue);
    display: flex; align-items: center; justify-content: center;
    color: var(--ink); font-weight: 700; font-size: 90px;
  }
  .back-notch {
    position: absolute; left: -14px; top: 150px;
    width: 30px; height: 150px; border-radius: 15px;
    background: var(--bg);
  }
  .back-details {
    position: absolute; left: 60px; top: 200px; color: var(--ink);
  }
  .back-name {
    color: var(--accent-blue); font-size: 28px; text-transform: uppercase;
    margin-bottom: 6px;
  }
  .back-role, .back-licence { font-size: 16px; line-height: 1.45; padding-left: 20px; }
  .contact-list { list-style: none; margin-top: 2px; }
  .contact-list li {
    display: flex; align-items: center; gap: 10px;
    font-size: 16px; line-height: 1.5;
  }
  .contact-list svg { width: 14px; height: 14px; flex: none; }
</style>
</head>
<body>

<section class="card card-front" aria-label="Card front">
  <div class="front-ghost-circle"></div>
  <div class="front-badge">MP</div>
  <div class="front-divider"></div>
  <h1 class="front-name"><span>Martin</span><span class="surname">Powles</span></h1>
  <p class="front-web">www.<span class="domain">martinpowles</span>.com.au</p>
  <p class="front-services">
    Renovations <i class="service-dot"></i> Bathrooms <i class="service-dot"></i> Decks
    <i class="service-dot"></i> Extensions <i class="service-dot"></i> New builds,
  </p>
</section>

<section class="card card-back" aria-label="Card back">
  <div class="back-disc"></div>
  <div class="back-badge">MP</div>
  <div class="back-notch"></div>
  <div class="back-details">
    <h2 class="back-name">Martin Powles</h2>
    <p class="back-role">Director</p>
    <p class="back-licence">Licence: (527691K)</p>
    <ul class="contact-list">
      <li>
        <svg viewBox="0 0 16 16" aria-hidden="true"><path d="M4 1.5l2.5 3-1.5 1.8a9 9 0 0 0 4.7 4.7l1.8-1.5 3 2.5-1.7 2.5C7.5 14.5 1.5 8.5 1.5 3.2z" fill="none" stroke="#27a7e0" stroke-width="1.5"/></svg>
        0400382415
      </li>
      <li>
        <svg viewBox="0 0 16 16" aria-hidden="true"><rect x="1.5" y="3.5" width="13" height="9" fill="none" stroke="#27a7e0" stroke-width="1.5"/><path d="M1.5 3.5l6.5 5 6.5-5" fill="none" stroke="#27a7e0" stroke-width="1.5"/></svg>
        info@martinpowles.com.au
      </li>
      <li class="contact-web">
        <svg viewBox="0 0 16 16" aria-hidden="true"><circle cx="8" cy="8" r="6.5" fill="none" stroke="#27a7e0" stroke-width="1.4"/><ellipse cx="8" cy="8" rx="2.8" ry="6.5" fill="none" stroke="#27a7e0" stroke-width="1.2"/><path d="M1.5 8h13" stroke="#27a7e0" stroke-width="1.2"/></svg>
        <span>www.<span class="domain">martinpowles</span>.com.au</span>
      </li>
    </ul>
  </div>
</section>

</body>
</html>
```